Varnor Immigration _Cloud-based, boutique law firm serving clients worldwide in US Immigration Law

I need a website for my new US immigration law firm that will be based in Montreal, QC Canada but serve clients worldwide to achieve their US immigration goals. This will be a boutique firm offering attentive and compassionate service to our corporate and individual clients. I'd like the site to be fresh, modern, sophisticated and easy to read.

I will need a home page, about/bio page, services page, and contact me page with a form so potential clients could email inquiries and also schedule consultations. I would also like a 'Book a Consultation' button on the home page (easily visible).

The longest website page is going to be the 'Services' tab, which I'd like to break down to services for Employers and services Individuals, with further sub-sets of services to each type of client. I envision images with short text that display longer text when hoovering over.

To start, I would have 3 subsets of services for Employers and 5 subsets of services for Individuals. I will need the ability to expand/edit these pages in Wix interface as we grow.

The site will need to be in English and in French.

I like the color blue and the final design should communicate the firm's core values: integrity and compassion. In other words, we do right, no matter what and are understanding to individual circumstances. I'd like the site to convey sophistication and accessibility. I don't like staged stock photos of people. Sites with a lot of stock photos of people feels unauthentic to me.

Logo draft is attached in jpeg. Navy and gold colors.
Example of 4 law firm sites I like below:
- https://www.quilbanelaw.example/
-https://www.zetrivlaw.example/
-https://harlowinappeals.example/
-https://www.ombrekilaw.example/

Target Market(s)

Small-medium sized businesses (10-999 employees) in US with foreign workforce; Foreign entrepreneurs wishing to implant in the US

Industry/Entity Type

Law

Coding

Font styles to use
Sans Serif

Colors

Designer to choose colors to be used in the design.

Requirements
Must have
• Great Home Page (Grabs attention with eye-catching images/text; Immediately establishes credibility; Provides an overview of services; Encourages visitor to take the next action.)
Nice to have
• Images of Montreal (where firm is based); Images of bridges (symbolizes progress, movement, connections)
Should not have
• Non-authentic photos: staged people at desks or pictures of court buildings.

```html
<!DOCTYPE html>
<html lang="en">
<head>
<meta charset="utf-8">
<title>Varnor Immigration Law</title>
<link href="https://fonts.googleapis.com/css2?family=Libre+Baskerville:ital,wght@0,400;0,700;1,400&family=Poppins:wght@400;500&display=swap" rel="stylesheet">
<style>
:root{
  --navy:#333b5a;
  --navy-dark:#2a3150;
  --gold:#c4a265;
  --gold-soft:#eadfc9;
  --white:#ffffff;
  --card:#f4f4f4;
  --ink:#333333;
  --muted:#c9ccd8;
  --serif:"Libre Baskerville", Georgia, serif;
  --sans:"Poppins", Arial, sans-serif;
}
*{margin:0;padding:0;box-sizing:border-box}
html,body{width:1200px;height:4204px;overflow:hidden}
body{position:relative;background:var(--white);font-family:var(--sans);color:var(--ink)}
.abs{position:absolute}
a{color:inherit;text-decoration:none}
h1,h2,h3,h4{font-weight:400}

/* header */
.site-header{left:0;top:0;width:1200px;height:109px;background:var(--navy)}
.brand{left:77px;top:24px;display:flex;align-items:center;gap:12px;color:var(--gold)}
.brand-mark{width:54px;height:54px;border-radius:50%;background:#8a8f9e}
.brand-name{font-family:var(--serif);font-size:18px;line-height:21px;letter-spacing:2px;text-transform:uppercase}
.brand-sub{font-family:var(--serif);font-size:8px;letter-spacing:1.5px;text-transform:uppercase}
.nav{top:46px;font-family:var(--serif);font-size:14px;color:var(--white);text-transform:uppercase}
.nav-lang{color:var(--gold)}
.btn-outline{border:1.5px solid var(--gold);color:var(--gold);font-family:var(--serif);font-size:14px;letter-spacing:1px;text-transform:uppercase;display:flex;align-items:center;justify-content:center}

/* hero */
.hero{left:0;top:109px;width:1200px;height:703px;background:linear-gradient(180deg,#8f8a86 0%,#6f6c6f 35%,#4d4b52 60%,#7b4a26 85%,#5a3b24 100%)}
.hero-shade{left:0;top:109px;width:1200px;height:703px;background:rgba(20,22,35,.25)}
.hero-title{left:0;top:330px;width:1200px;text-align:center;font-family:var(--serif);font-weight:700;font-size:64px;color:var(--white);letter-spacing:2px}
.hero-sub{left:0;top:412px;width:1200px;text-align:center;font-family:var(--serif);font-style:italic;font-weight:700;font-size:28px;line-height:39px;color:var(--white)}

/* shared */
.eyebrow{font-family:var(--serif);font-style:italic;font-size:21px;color:var(--gold)}
.section-title{font-family:var(--serif);font-weight:400;font-size:31px;text-transform:uppercase;letter-spacing:.5px}
.copy{font-size:15px;line-height:30px}
.btn-gold{background:var(--gold);color:var(--white);font-family:var(--serif);font-weight:700;font-size:18px;letter-spacing:1px;text-transform:uppercase;display:flex;align-items:center;justify-content:center}
.arrow-btn{width:44px;height:43px;display:flex;align-items:center;justify-content:center;border-radius:3px}
.arrow-gold{background:var(--gold)}
.arrow-navy{background:var(--navy)}

/* about + services */
.about-panel{left:75px;top:888px;width:1125px;height:933px;background:var(--navy);border-radius:65px 0 0 65px}
.bridge-photo{left:0;top:962px;width:496px;height:434px;background:linear-gradient(180deg,#6f8fb8 0%,#c99aa3 45%,#e79a6a 60%,#6a5d6a 100%);border-radius:0 0 26px 0}
.light{color:var(--white)}
.service-card{top:1671px;width:302px;height:307px;background:var(--card);border-radius:6px;box-shadow:0 2px 8px rgba(0,0,0,.15);text-align:center}
.service-visual{width:86px;height:84px;margin:20px auto 0;border-radius:8px;background:var(--gold-soft)}
.service-name{font-family:var(--serif);font-weight:700;font-size:22px;color:var(--navy);letter-spacing:1px;margin-top:10px}
.service-text{font-size:15px;line-height:27px;color:var(--ink);margin:8px 24px 0}
.service-link{margin-top:14px}

/* team */
.team-panel{left:0;top:2053px;width:1127px;height:813px;background:var(--navy);border-radius:0 65px 65px 0}
.gold-block{left:692px;top:2113px;width:128px;height:154px;background:var(--gold)}
.team-photo{left:705px;top:2126px;width:495px;height:433px;background:linear-gradient(135deg,#dcdcdc 0%,#c9c9c9 55%,#bfbfbf 100%);border-radius:10px 0 0 10px}

/* testimonials */
.testimonial{left:105px;top:2654px;width:989px;height:426px;background:var(--card);border-radius:8px;box-shadow:0 2px 10px rgba(0,0,0,.15)}
.avatar{left:550px;top:2792px;width:98px;height:98px;border-radius:50%;background:linear-gradient(160deg,#8a6048,#4a3328)}
.quote{left:160px;top:2904px;width:880px;text-align:center;font-size:15px;line-height:30px;font-style:italic;color:var(--ink)}
.quote-name{left:0;top:3008px;width:1200px;text-align:center;font-family:var(--serif);font-weight:700;font-size:16px;letter-spacing:1px;color:var(--gold)}

/* blog */
.post-img{top:3258px;height:204px}
.post-strip{top:3462px;width:28px;height:88px;background:var(--navy-dark)}
.post-title{top:3486px;font-family:var(--serif);font-weight:400;font-size:21px;line-height:29px;color:var(--navy);text-transform:uppercase;letter-spacing:.5px}
.post-date{top:3586px;font-family:var(--serif);font-weight:700;font-size:14px;color:var(--gold)}

/* footer */
.site-footer{left:0;top:3686px;width:1200px;height:454px;background:var(--navy)}
.footer-bar{left:0;top:4140px;width:1200px;height:64px;background:var(--navy-dark)}
.footer-heading{font-family:var(--serif);font-weight:700;font-size:16px;letter-spacing:1px;color:var(--white);text-transform:uppercase}
.footer-links{list-style:none;margin-top:14px}
.footer-links li{font-size:14px;line-height:32.5px;color:var(--muted);text-transform:uppercase}
.address-box{left:794px;top:3756px;width:333px;height:313px;border:1px solid #6c7291;padding:34px 22px}
.address-row{display:flex;gap:14px;font-size:14px;line-height:28px;color:var(--muted);text-transform:uppercase;margin-top:8px}
.address-row svg{flex:none;margin-top:7px}
.email-input{left:75px;top:4015px;width:392px;height:54px;background:var(--white);font-size:13px;color:#444;padding-left:16px;display:flex;align-items:center}
.signup{left:467px;top:4015px;width:98px;height:54px;font-size:15px}
.copyright{left:75px;top:4163px;font-size:13px;color:var(--muted)}
.social{top:4162px;display:flex;gap:16px}
.social span{width:18px;height:18px;border-radius:50%;background:#8a90a8;display:block}
</style>
</head>
<body>

<header class="site-header abs"></header>
<div class="brand abs">
  <span class="brand-mark"></span>
  <div>
    <div class="brand-name">Varnor<br>Immigration</div>
    <div class="brand-sub">Maren Varnor, Attorney</div>
  </div>
</div>
<nav>
  <a class="nav abs" style="left:343px">Home</a>
  <a class="nav abs" style="left:429px">About Us</a>
  <a class="nav abs" style="left:547px">Services
    <svg width="10" height="8" viewBox="0 0 10 8" style="margin-left:6px"><path d="M1 2l4 4 4-4" stroke="#fff" stroke-width="2" fill="none"/></svg></a>
  <a class="nav abs" style="left:686px">Contact Us</a>
  <a class="nav nav-lang abs" style="left:813px">EN
    <svg width="10" height="8" viewBox="0 0 10 8"><path d="M1 2l4 4 4-4" stroke="#c4a265" stroke-width="2" fill="none"/></svg></a>
</nav>
<a class="btn-outline abs" style="left:874px;top:31px;width:253px;height:47px">Book a Consultation</a>

<section>
  <div class="hero abs" role="img" aria-label="Montreal skyline in autumn at sunset"></div>
  <div class="hero-shade abs"></div>
  <h1 class="hero-title abs">Varnor Immigration Law</h1>
  <p class="hero-sub abs">We are a Cloud-based, boutique law firm serving clients<br>worldwide in US Immigration Law.</p>
  <a class="btn-outline abs" style="left:474px;top:511px;width:253px;height:47px">Book a Consultation</a>
</section>

<section>
  <div class="about-panel abs"></div>
  <div class="bridge-photo abs" role="img" aria-label="Suspension bridge over a river at sunset"></div>
  <p class="eyebrow abs" style="left:524px;top:980px">Welcome</p>
  <h2 class="section-title abs light" style="left:524px;top:1014px">About Varnor Immigration</h2>
  <p class="copy abs light" style="left:524px;top:1068px;width:610px">Nemo enim ipsam voluptatem quia voluptas sit aspernatur aut odit aut fugit, sed quia consequuntur magni dolores eos qui ratione voluptatem sequi nesciunt. Neque porro quisquam est, qui dolorem ipsum quia dolor sit amet, consectetur, adipisci velit, sed quia non numquam.</p>
  <p class="copy abs light" style="left:524px;top:1203px;width:610px">Neque porro quisquam est, qui dolorem ipsum quia dolor sit amet, consectetur, adipisci velit, sed quia non numquam eius modi tempora cdunt ut labore et dolore magnam aliquam quaerat voluptatem.</p>
  <a class="btn-gold abs" style="left:524px;top:1323px;width:180px;height:52px">Read More</a>

  <p class="eyebrow abs" style="left:101px;top:1465px">What We Do</p>
  <h2 class="section-title abs light" style="left:101px;top:1500px">Our Services</h2>
  <p class="copy abs light" style="left:101px;top:1551px;width:940px">Neque porro quisquam est, qui dolorem ipsum quia dolor sit amet,<br>consectetur, adipisci velit, sed quia non numquam eius modi tempora cdunt ut labore et dolore magnam aliquam<br>quaerat voluptatem.</p>

  <article class="service-card abs" style="left:101px">
    <div class="service-visual" role="img" aria-label="Passport service illustration"></div>
    <h3 class="service-name">NEQUE PORRO</h3>
    <p class="service-text">Nemo enim ipsam voluptatem quia voluptas sit aspernatur aut odit aut fugit.</p>
    <svg class="service-link" width="20" height="20" viewBox="0 0 20 20"><circle cx="10" cy="10" r="9" fill="#c4a265"/><path d="M7 6l4 4-4 4" stroke="#fff" stroke-width="2" fill="none"/></svg>
  </article>
  <article class="service-card abs" style="left:434px">
    <div class="service-visual" role="img" aria-label="Application review service illustration"></div>
    <h3 class="service-name">NEQUE PORRO</h3>
    <p class="service-text">Nemo enim ipsam voluptatem quia voluptas sit aspernatur aut odit aut fugit.</p>
    <svg class="service-link" width="20" height="20" viewBox="0 0 20 20"><circle cx="10" cy="10" r="9" fill="#c4a265"/><path d="M7 6l4 4-4 4" stroke="#fff" stroke-width="2" fill="none"/></svg>
  </article>
  <article class="service-card abs" style="left:766px">
    <div class="service-visual" role="img" aria-label="Global mobility service illustration"></div>
    <h3 class="service-name">NEQUE PORRO</h3>
    <p class="service-text">Nemo enim ipsam voluptatem quia voluptas sit aspernatur aut odit aut fugit.</p>
    <svg class="service-link" width="20" height="20" viewBox="0 0 20 20"><circle cx="10" cy="10" r="9" fill="#c4a265"/><path d="M7 6l4 4-4 4" stroke="#fff" stroke-width="2" fill="none"/></svg>
  </article>
  <a class="arrow-btn arrow-gold abs" style="left:1083px;top:1878px"><svg width="14" height="20" viewBox="0 0 14 20"><path d="M4 3l7 7-7 7" stroke="#fff" stroke-width="2" fill="none"/></svg></a>
  <a class="arrow-btn arrow-navy abs" style="left:1083px;top:1934px"><svg width="14" height="20" viewBox="0 0 14 20"><path d="M10 3l-7 7 7 7" stroke="#fff" stroke-width="2" fill="none"/></svg></a>
</section>

<section>
  <div class="team-panel abs"></div>
  <div class="gold-block abs"></div>
  <div class="team-photo abs" role="img" aria-label="Portrait of the firm's attorney"></div>
  <p class="eyebrow abs" style="left:73px;top:2198px">Our People</p>
  <h2 class="section-title abs light" style="left:73px;top:2232px">Meet Our Team</h2>
  <p class="copy abs light" style="left:73px;top:2287px;width:610px">Nemo enim ipsam voluptatem quia voluptas sit aspernatur aut odit aut fugit, sed quia consequuntur magni dolores eos qui ratione voluptatem sequi nesciunt. Neque porro quisquam est, qui dolorem ipsum quia dolor sit amet, consectetur, adipisci velit, sed quia non numquam.</p>
  <a class="btn-gold abs" style="left:75px;top:2435px;width:180px;height:51px">Read More</a>
</section>

<section>
  <div class="testimonial abs"></div>
  <p class="eyebrow abs" style="left:0;top:2703px;width:1200px;text-align:center">What Our Client Says About Us</p>
  <h2 class="section-title abs" style="left:0;top:2737px;width:1200px;text-align:center;color:var(--ink)">Testimonials</h2>
  <div class="avatar abs" role="img" aria-label="Client portrait"></div>
  <p class="quote abs">“ Nemo enim ipsam voluptatem quia voluptas sit aspernatur aut odit aut fugit, sed quia consequuntur magni dolores eos qui ratione voluptatem sequi nesciunt. Neque porro quisquam est, qui dolorem ipsum quia dolor sit amet, consectetur, adipisci velit, sed quia non numquam..”</p>
  <p class="quote-name abs">Name Heading</p>
  <svg class="abs" style="left:122px;top:2856px" width="14" height="20" viewBox="0 0 14 20"><path d="M10 3l-7 7 7 7" stroke="#555" stroke-width="2" fill="none"/></svg>
  <svg class="abs" style="left:1064px;top:2856px" width="14" height="20" viewBox="0 0 14 20"><path d="M4 3l7 7-7 7" stroke="#555" stroke-width="2" fill="none"/></svg>
</section>

<section>
  <p class="eyebrow abs" style="left:73px;top:3150px">What's New</p>
  <h2 class="section-title abs" style="left:73px;top:3184px;color:var(--ink)">Latest Blog Posts</h2>
  <a class="arrow-btn arrow-navy abs" style="left:1024px;top:3163px"><svg width="14" height="20" viewBox="0 0 14 20"><path d="M10 3l-7 7 7 7" stroke="#fff" stroke-width="2" fill="none"/></svg></a>
  <a class="arrow-btn arrow-gold abs" style="left:1083px;top:3163px"><svg width="14" height="20" viewBox="0 0 14 20"><path d="M4 3l7 7-7 7" stroke="#fff" stroke-width="2" fill="none"/></svg></a>

  <div class="post-img abs" style="left:75px;width:328px;background:linear-gradient(180deg,#6d9ad0,#b79a4e 60%,#7a7366)" role="img" aria-label="Yellow arch bridge in a city"></div>
  <div class="post-strip abs" style="left:375px"></div>
  <h3 class="post-title abs" style="left:75px;width:300px">Excepteur Sint<br>Occaecat Cupidatat<br>Non Proident</h3>
  <p class="post-date abs" style="left:75px">Jan17, 2023</p>

  <div class="post-img abs" style="left:436px;width:330px;background:linear-gradient(180deg,#8a9bb0,#b9b4ad 45%,#4b4b4e)" role="img" aria-label="Open road with the word immigration painted on it"></div>
  <div class="post-strip abs" style="left:738px"></div>
  <h3 class="post-title abs" style="left:436px;width:300px">Excepteur Sint<br>Occaecat Cupidatat<br>Non Proident</h3>
  <p class="post-date abs" style="left:436px">Jan17, 2023</p>

  <div class="post-img abs" style="left:798px;width:329px;background:linear-gradient(135deg,#b7b94a,#9fa4a8 45%,#3f4a63)" role="img" aria-label="Traveller in an airport terminal"></div>
  <div class="post-strip abs" style="left:1099px"></div>
  <h3 class="post-title abs" style="left:798px;width:300px">Excepteur Sint<br>Occaecat Cupidatat<br>Non Proident</h3>
  <p class="post-date abs" style="left:798px">Jan17, 2023</p>
</section>

<footer>
  <div class="site-footer abs"></div>
  <div class="abs" style="left:75px;top:3754px">
    <h4 class="footer-heading">Quick Links</h4>
    <ul class="footer-links"><li>Home</li><li>About Us</li><li>Services</li><li>Contact Us</li></ul>
  </div>
  <div class="abs" style="left:312px;top:3754px">
    <h4 class="footer-heading">Services</h4>
    <ul class="footer-links"><li>Sed utperspiciatis</li><li>Unde omnis</li><li>Iste natus error</li><li>Sit volupta</li><li>Tem accusant</li></ul>
  </div>
  <div class="abs" style="left:565px;top:3754px">
    <h4 class="footer-heading">Legal</h4>
    <ul class="footer-links"><li>Sed utperspiciatis</li><li>Unde omnis</li><li>Iste natus error</li><li>Sit volupta</li><li>Tem accusant</li></ul>
  </div>
  <div class="address-box abs">
    <h4 class="footer-heading">Address Information</h4>
    <div class="address-row" style="margin-top:14px"><svg width="14" height="12" viewBox="0 0 14 12"><path d="M1 2l4-1 4 2 4-1v9l-4 1-4-2-4 1z" fill="#c4a265"/></svg><span>Sed ut perspiciatis unde<br>omnis iste natus</span></div>
    <div class="address-row"><svg width="14" height="14" viewBox="0 0 14 14"><path d="M3 1l3 3-2 2c1 2 2 3 4 4l2-2 3 3-2 2C6 13 1 8 1 3z" fill="#c4a265"/></svg><span>1-800-555-0142</span></div>
    <div class="address-row"><svg width="14" height="12" viewBox="0 0 14 12"><path d="M1 2l4-1 4 2 4-1v9l-4 1-4-2-4 1z" fill="#c4a265"/></svg><span>1-800-555-0142</span></div>
    <div class="address-row"><svg width="14" height="14" viewBox="0 0 14 14"><path d="M3 1l3 3-2 2c1 2 2 3 4 4l2-2 3 3-2 2C6 13 1 8 1 3z" fill="#c4a265"/></svg><span>info@varnorlaw.example</span></div>
    <div class="address-row"><svg width="12" height="14" viewBox="0 0 12 14"><path d="M6 0a5 5 0 015 5c0 4-5 9-5 9S1 9 1 5a5 5 0 015-5z" fill="#c4a265"/><circle cx="6" cy="5" r="2" fill="#333b5a"/></svg><span style="color:#fff">Map Direction</span></div>
  </div>
  <h4 class="footer-heading abs" style="left:75px;top:3982px">Newsletter Subscribe</h4>
  <div class="email-input abs">Enter Email Address</div>
  <a class="btn-gold signup abs">Sign Up</a>
  <div class="footer-bar abs"></div>
  <p class="copyright abs">Copyright © 2023. Company Name All Rights Reserved</p>
  <div class="social abs" style="left:962px"><span></span><span></span><span></span><span></span><span></span></div>
</footer>

</body>
</html>
```